Quendra Website re-design with new logo and look

Refresh on current website. Incorporate new logo which is attached. We provide technology SAAS services to the healthcare space. Current website is at quendra.com but the new name is Quendra.com (see logo) Key considerations are as follows:
1. Incorporate a promo video location. I have a new video coming out similar to this one. https://www.portvane.net/gallery/41736520/Mobile-Application-Promo
2. Incorporate platform features section. as an example see this website where it has mini screens that call out various features ie; "all in one GCR platform" see webiste https://www.pelvox.io/
3. Add some color splash from the log throughout the website
4. Where possible use the text from our website Quendra.com where not possible use lorem ipsum and we will complete
5. use current theme colors
6. Please use your skills to make it more functional and useful and not replicate what we have.

Target Market(s)

Imaging centers and hospitals

Industry/Entity Type

Healthcare

Coding

Coded - Design and coding required

Number of Pages Required

5+ page

Font styles to use
Sans Serif

Requirements
Must have
• Note section in this website that shows features of the platform as you scoll down. See website https://www.pelvox.io/
Nice to have
• Professional look only, keep current color scheme but add in some splash of color from the logo
Should not have
• animated characters or cartoon drawings

```html
<!DOCTYPE html>
<html lang="en">
<head>
<meta charset="UTF-8">
<title>Quendra — Technology for Healthcare</title>
<link href="https://fonts.googleapis.com/css2?family=Poppins:wght@300;400;500;600;700&display=swap" rel="stylesheet">
<style>
:root{
  --teal:#3fc5d4;
  --teal-deep:#27aebf;
  --teal-light:#62d3de;
  --orange:#f7a234;
  --orange-footer:#f9a63f;
  --navy:#0c4457;
  --navy-deep:#08303f;
  --ink:#111418;
  --text:#444a50;
  --grey-bg:#f1f1f1;
  --ice:#e3f5f8;
  --white:#ffffff;
}
*{margin:0;padding:0;box-sizing:border-box}
html,body{width:1200px;height:4934px;overflow:hidden}
body{font-family:'Poppins',sans-serif;color:var(--ink);background:var(--white);position:relative}
section,header,footer{position:absolute;left:0;width:1200px}
.abs{position:absolute}
.btn{position:absolute;background:var(--orange);color:var(--white);border-radius:30px;display:flex;align-items:center;justify-content:center;font-weight:500}
.dot{display:inline-block;border-radius:50%;background:var(--orange);flex:none}
.section-title{position:absolute;left:0;width:1200px;display:flex;align-items:center;justify-content:center;gap:22px;font-weight:600;font-size:56px;letter-spacing:-.5px}
.section-title .dot{width:60px;height:60px}

/* header */
.site-header{top:0;height:119px}
.brand{position:absolute;left:70px;top:28px;display:flex;align-items:center;gap:14px;font-weight:600;font-size:42px;letter-spacing:2px;color:var(--ink)}
.brand .dot{width:56px;height:56px}
.topbar{position:absolute;left:533px;top:0;width:667px;height:67px}
.topbar svg{position:absolute;left:0;top:0}
.contact-chip{position:absolute;top:18px;display:flex;align-items:center;gap:8px;color:var(--white);font-size:10px;line-height:13px}
.chip-icon{width:28px;height:28px;border-radius:50%;background:var(--white);display:flex;align-items:center;justify-content:center}
.top-social{position:absolute;top:20px;display:flex;gap:10px;left:489px}
.top-social span{width:22px;height:22px;border-radius:50%;border:2px solid var(--white)}
.nav{position:absolute;top:82px;left:632px;display:flex;font-size:14px;color:var(--ink)}
.nav a{position:absolute;white-space:nowrap;text-decoration:none;color:inherit}
.nav a.active{border-bottom:2px solid var(--teal);padding-bottom:3px}

/* hero */
.hero{top:119px;height:437px;background:var(--teal)}
.hero-visual{position:absolute;left:0;top:0;width:640px;height:437px;background:linear-gradient(90deg,#0d5f6c 0%,#1d8f9f 45%,var(--teal) 100%)}
.hero h1{position:absolute;left:587px;top:82px;font-weight:600;font-size:60px;line-height:82px;color:var(--white);letter-spacing:.5px}
.hero p{position:absolute;left:590px;top:247px;font-size:33px;font-weight:400;color:var(--white)}
.hero .btn{left:590px;top:318px;width:183px;height:44px;font-size:20px}

/* solutions */
.solutions{top:556px;height:565px}
.solutions .section-title{top:62px}
.sol-card{position:absolute;top:197px;width:246px;height:301px;background:var(--white);box-shadow:0 2px 10px rgba(0,0,0,.16)}
.sol-icon{position:absolute;left:38px;top:21px;width:170px;height:152px;background:var(--teal);border-radius:8px}
.sol-icon::before{content:"";position:absolute;inset:10px;border:2px dashed rgba(255,255,255,.85);border-radius:6px}
.sol-icon svg{position:absolute;left:50px;top:41px}
.sol-card h3{position:absolute;top:190px;width:100%;text-align:center;font-size:17px;font-weight:500}
.sol-card .btn{left:63px;top:238px;width:120px;height:34px;font-size:12px}

/* markets */
.markets{top:1121px;height:619px;background:var(--grey-bg)}
.markets .section-title{top:80px}
.market{position:absolute;top:199px;width:190px;height:395px;color:var(--white);text-align:center}
.market svg.shape{position:absolute;left:0;top:0}
.market .m-icon{position:absolute;left:55px;top:22px}
.market h3{position:absolute;top:132px;width:100%;font-size:20px;font-weight:600;line-height:26px}
.market p{position:absolute;top:180px;left:16px;width:158px;font-size:14px;line-height:22px;font-weight:400}
.market.two p{top:206px}

/* tech band */
.tech-band{top:1740px;height:383px;background:radial-gradient(ellipse at 30% 40%,#1e6d86 0%,var(--navy) 55%,var(--navy-deep) 100%);color:var(--white);text-align:center}
.tech-band .section-title{top:76px;color:var(--white);font-size:58px}
.tech-band .section-title .dot{background:var(--white)}
.tech-band h3{position:absolute;top:165px;width:100%;font-size:40px;font-weight:300}
.tech-band p{position:absolute;top:248px;left:220px;width:760px;font-size:20px;line-height:26px;font-weight:300}

/* promo */
.promo{top:2123px;height:812px;background:var(--grey-bg)}
.promo .section-title{top:76px}
.video-frame{position:absolute;left:159px;top:199px;width:903px;height:407px;background:var(--white);box-shadow:0 2px 12px rgba(0,0,0,.15)}
.video-still{position:absolute;left:24px;top:28px;width:855px;height:350px;background:linear-gradient(180deg,#5c5d62 0%,#9a9a9c 45%,#6b6f76 100%)}
.video-still svg{position:absolute;left:387px;top:135px}
.promo p{position:absolute;left:160px;top:646px;width:880px;text-align:center;font-size:17px;line-height:24px;color:var(--text)}

/* platform */
.platform{top:2935px;height:376px;background:var(--ice)}
.dash{position:absolute;left:96px;top:88px;width:469px;height:230px;background:var(--white);box-shadow:0 2px 8px rgba(0,0,0,.08);font-size:7px;color:#888}
.platform h2{position:absolute;left:594px;top:100px;display:flex;align-items:center;gap:10px;font-size:31px;font-weight:600}
.platform h2 .dot{width:34px;height:34px}
.platform p{position:absolute;left:598px;top:170px;width:504px;font-size:14.5px;line-height:24px;text-align:justify;color:var(--text)}

/* cases */
.cases{top:3311px;height:689px}
.cases .section-title{top:56px}
.case{position:absolute;background:var(--white);box-shadow:0 2px 12px rgba(0,0,0,.16)}
.case .photo{position:absolute;left:12px;top:12px;right:12px}
.case h3{position:absolute;left:20px;right:20px;font-size:16px;font-weight:500;line-height:19px}
.case p{position:absolute;left:20px;right:20px;font-size:13.5px;line-height:17px;color:var(--text)}
.case .btn{font-size:11px;height:22px;width:80px}
.arrow{position:absolute;top:3700px;width:46px;height:46px;border-radius:50%;background:#cdeef3;display:flex;align-items:center;justify-content:center}

/* cta */
.cta{top:4000px;height:483px;background:radial-gradient(ellipse at 70% 30%,#1a6680 0%,var(--navy) 55%,var(--navy-deep) 100%);color:var(--white);text-align:center}
.cta h2{position:absolute;top:72px;width:100%;font-size:60px;line-height:72px;font-weight:600}
.cta p{position:absolute;top:237px;width:100%;font-size:29px;line-height:50px}
.cta .btn{left:521px;top:366px;width:179px;height:50px;font-size:22px}

/* footer */
.site-footer{top:4483px;height:451px;background:var(--orange-footer);color:var(--white)}
.f-brand{position:absolute;left:118px;top:92px;display:flex;flex-direction:column;align-items:center;gap:14px;font-size:34px;font-weight:500;letter-spacing:3px}
.f-brand .dot{width:70px;height:70px;background:var(--white)}
.f-social{position:absolute;left:116px;top:262px;display:flex;gap:12px}
.f-social span{width:36px;height:36px;border-radius:50%;background:var(--white)}
.f-col{position:absolute;top:96px}
.f-col h4{font-size:22px;font-weight:500;margin-bottom:22px}
.f-links{list-style:none;font-size:13px;line-height:27px}
.f-links li::before{content:"";display:inline-block;width:6px;height:6px;border-radius:50%;background:var(--white);margin-right:16px;vertical-align:middle}
.f-contact{display:flex;gap:12px;font-size:15px;line-height:23px;margin-bottom:22px}
.f-contact .chip-icon{width:34px;height:34px;margin-top:4px}
.f-news p{font-size:14px;line-height:23px;width:300px}
.f-input{position:absolute;top:137px;left:2px;width:303px;height:44px;background:var(--white);border-radius:8px;color:#999;font-size:13px;padding:13px 22px}
.f-sub{position:absolute;top:205px;left:4px;width:135px;height:32px;border:2px solid var(--white);border-radius:20px;font-size:14px;display:flex;align-items:center;justify-content:center}
.f-rule{position:absolute;left:66px;width:1068px;top:375px;border-top:1px solid rgba(255,255,255,.5)}
.f-copy{position:absolute;top:405px;width:100%;text-align:center;font-size:13px}
</style>
</head>
<body>

<header class="site-header">
  <div class="brand"><span class="dot"></span>QUENDRA</div>
  <div class="topbar">
    <svg width="667" height="67"><polygon points="22,0 667,0 667,67 0,67" fill="var(--teal)"/></svg>
    <div class="contact-chip" style="left:164px"><span class="chip-icon"><svg width="14" height="10"><rect x="0.5" y="0.5" width="13" height="9" rx="1" fill="none" stroke="#e4573a"/><polyline points="0.5,0.5 7,6 13.5,0.5" fill="none" stroke="#e4573a"/></svg></span><div>EMAIL:<br>hello@quendra.com</div></div>
    <div class="contact-chip" style="left:340px"><span class="chip-icon"><svg width="14" height="14" viewBox="0 0 24 24"><path d="M6.6 10.8a15 15 0 0 0 6.6 6.6l2.2-2.2c.3-.3.7-.4 1-.2 1.1.4 2.3.6 3.6.6.6 0 1 .4 1 1V20c0 .6-.4 1-1 1A17 17 0 0 1 3 4c0-.6.4-1 1-1h3.5c.6 0 1 .4 1 1 0 1.3.2 2.5.6 3.6.1.3 0 .7-.2 1z" fill="var(--teal)"/></svg></span><div>PHONE<br>1-555-014-2290</div></div>
    <div class="top-social"><span></span><span></span><span></span><span></span></div>
  </div>
  <nav class="nav">
    <a class="active" style="left:0">Home</a>
    <a style="left:72px">Solutions</a>
    <a style="left:168px">Markets</a>
    <a style="left:265px">Case Studies</a>
  </nav>
  <div class="btn" style="left:1026px;top:80px;width:111px;height:29px;font-size:13px;font-weight:400">Get Started</div>
</header>

<section class="hero">
  <div class="hero-visual" role="img" aria-label="Hand touching a glowing digital interface of healthcare technology icons"></div>
  <h1>TECHNOLOGY FOR<br>HEALTHCARE</h1>
  <p>What's your Vision?</p>
  <div class="btn">Know More</div>
</section>

<section class="solutions">
  <h2 class="section-title"><span class="dot"></span>SOLUTIONS</h2>
  <div class="sol-card" style="left:86px">
    <div class="sol-icon"><svg width="70" height="70" fill="none" stroke="#fff" stroke-width="2.5"><rect x="5" y="8" width="60" height="40" rx="3"/><line x1="35" y1="48" x2="35" y2="60"/><line x1="20" y1="62" x2="50" y2="62"/><circle cx="35" cy="28" r="11"/><circle cx="35" cy="28" r="3" fill="#fff"/></svg></div>
    <h3>Teleradiology</h3><div class="btn">View More</div>
  </div>
  <div class="sol-card" style="left:347px">
    <div class="sol-icon"><svg width="70" height="70" fill="none" stroke="#fff" stroke-width="2.5"><rect x="8" y="8" width="40" height="56" rx="3"/><rect x="20" y="3" width="16" height="9" rx="2"/><path d="M24 22h8M28 18v8"/><line x1="16" y1="36" x2="40" y2="36"/><line x1="16" y1="44" x2="40" y2="44"/><circle cx="54" cy="52" r="11"/><polyline points="49,52 53,56 59,48"/></svg></div>
    <h3>Clinical</h3><div class="btn">View More</div>
  </div>
  <div class="sol-card" style="left:608px">
    <div class="sol-icon"><svg width="70" height="70" fill="none" stroke="#fff" stroke-width="2.5"><rect x="8" y="6" width="42" height="58" rx="3"/><polyline points="14,18 17,21 22,15"/><line x1="27" y1="18" x2="42" y2="18"/><polyline points="14,32 17,35 22,29"/><line x1="27" y1="32" x2="42" y2="32"/><polyline points="14,46 17,49 22,43"/><line x1="27" y1="46" x2="38" y2="46"/><path d="M54 42l10 4v8c0 6-5 9-10 11-5-2-10-5-10-11v-8z"/></svg></div>
    <h3>Compliance</h3><div class="btn">View More</div>
  </div>
  <div class="sol-card" style="left:868px">
    <div class="sol-icon"><svg width="70" height="70" fill="none" stroke="#fff" stroke-width="2.5"><rect x="8" y="46" width="8" height="16"/><rect x="22" y="38" width="8" height="24"/><rect x="36" y="30" width="8" height="32"/><rect x="50" y="22" width="8" height="40"/><polyline points="8,34 24,22 34,26 56,6"/><polyline points="46,6 56,6 56,16"/></svg></div>
    <h3>PACS and RIS</h3><div class="btn">View More</div>
  </div>
</section>

<section class="markets">
  <h2 class="section-title"><span class="dot"></span>WATCH THE VIDEO</h2>

  <div class="market" style="left:82px">
    <svg class="shape" width="190" height="395"><polygon points="0,0 190,22 190,300 0,318" fill="var(--teal-deep)"/><polygon points="18,312 172,294 172,330 108,395 18,395" fill="var(--teal-light)"/><polyline points="76,332 90,345 76,358 M94,332 108,345 94,358" fill="none" stroke="#fff" stroke-width="5"/></svg>
    <svg class="m-icon" width="80" height="80" fill="none" stroke="#fff" stroke-width="2.5"><rect x="16" y="22" width="48" height="54"/><rect x="30" y="4" width="20" height="18"/><path d="M40 8v10M35 13h10"/><rect x="24" y="32" width="8" height="8"/><rect x="48" y="32" width="8" height="8"/><rect x="24" y="48" width="8" height="8"/><rect x="48" y="48" width="8" height="8"/><rect x="34" y="60" width="12" height="16"/></svg>
    <h3>HOSPITALS</h3><p>Lorem Ipsum is simply dummy text of the printing and</p>
  </div>
  <div class="market" style="left:295px">
    <svg class="shape" width="190" height="395"><polygon points="0,0 190,22 190,300 0,318" fill="var(--teal-deep)"/><polygon points="18,312 172,294 172,330 108,395 18,395" fill="var(--teal-light)"/><polyline points="76,332 90,345 76,358 M94,332 108,345 94,358" fill="none" stroke="#fff" stroke-width="5"/></svg>
    <svg class="m-icon" width="80" height="80" fill="none" stroke="#fff" stroke-width="2.5"><path d="M40 6l28 10v20c0 18-13 30-28 38-15-8-28-20-28-38V16z"/><circle cx="40" cy="38" r="14"/><path d="M40 31v14M33 38h14"/></svg>
    <h3>URGENT CARE</h3><p>Lorem Ipsum is simply dummy text of the printing and</p>
  </div>
  <div class="market two" style="left:508px">
    <svg class="shape" width="190" height="395"><polygon points="0,0 190,22 190,300 0,318" fill="var(--teal-deep)"/><polygon points="18,312 172,294 172,330 108,395 18,395" fill="var(--teal-light)"/><polyline points="76,332 90,345 76,358 M94,332 108,345 94,358" fill="none" stroke="#fff" stroke-width="5"/></svg>
    <svg class="m-icon" width="80" height="80" fill="none" stroke="#fff" stroke-width="2.5"><polygon points="40,6 72,24 8,24"/><line x1="12" y1="30" x2="68" y2="30"/><line x1="20" y1="34" x2="20" y2="64"/><line x1="34" y1="34" x2="34" y2="64"/><line x1="46" y1="34" x2="46" y2="64"/><line x1="60" y1="34" x2="60" y2="64"/><rect x="8" y="66" width="64" height="8"/></svg>
    <h3>GOVERNMENT<br>HEALTH</h3><p>Lorem Ipsum is simply dummy text of the printing and</p>
  </div>
  <div class="market" style="left:721px">
    <svg class="shape" width="190" height="395"><polygon points="0,0 190,22 190,300 0,318" fill="var(--teal-deep)"/><polygon points="18,312 172,294 172,330 108,395 18,395" fill="var(--teal-light)"/><polyline points="76,332 90,345 76,358 M94,332 108,345 94,358" fill="none" stroke="#fff" stroke-width="5"/></svg>
    <svg class="m-icon" width="80" height="80" fill="none" stroke="#fff" stroke-width="2.5"><path d="M40 42C24 30 18 24 18 16a10 10 0 0 1 22-4 10 10 0 0 1 22 4c0 8-6 14-22 26z"/><polyline points="24,22 32,22 36,14 42,28 46,20 56,20"/><path d="M6 54h18l12 8h18c4 0 4 6 0 6H38M6 72h30l34-16c4-2 2-8-3-6l-17 6"/></svg>
    <h3>ACUTE CARE</h3><p>Lorem Ipsum is simply dummy text of the printing and</p>
  </div>
  <div class="market" style="left:934px">
    <svg class="shape" width="190" height="395"><polygon points="0,0 190,22 190,300 0,318" fill="var(--teal-deep)"/><polygon points="18,312 172,294 172,330 108,395 18,395" fill="var(--teal-light)"/><polyline points="76,332 90,345 76,358 M94,332 108,345 94,358" fill="none" stroke="#fff" stroke-width="5"/></svg>
    <svg class="m-icon" width="80" height="80" fill="none" stroke="#fff" stroke-width="2.5"><path d="M34 44h12v-12h12v12h12v12H58v12H46V56H34z"/><circle cx="28" cy="24" r="14"/></svg>
    <h3>VETERINARIAN</h3><p>Lorem Ipsum is simply dummy text of the printing and</p>
  </div>
</section>

<section class="tech-band">
  <h2 class="section-title"><span class="dot"></span>TECHNOLOGY FOR YOU!</h2>
  <h3>Purpose built Technology</h3>
  <p>Our end to end workflow platform is purposely built for remote access from anywhere in the world while providing &nbsp;centralized management access.</p>
</section>

<section class="promo">
  <h2 class="section-title"><span class="dot"></span>WATCH THE VIDEO</h2>
  <div class="video-frame">
    <div class="video-still" role="img" aria-label="Promo video still of a diverse healthcare business team standing together">
      <svg width="82" height="82"><circle cx="41" cy="41" r="37" fill="none" stroke="#fff" stroke-width="5"/><polygon points="32,24 60,41 32,58" fill="#fff"/></svg>
    </div>
  </div>
  <p>There are many variations of passages of Lorem Ipsum available, but the majority have suffered alteration in some form, by injected humour, or randomised words which don't look even slightly believable. If you are going to use a passage of Lorem Ipsum, you need to be sure there isn't anything embarrassing hidden in the middle of text. All the Lorem Ipsum generators on the Internet tend to repeat predefined chunks as necessary, making this the first true generator on the Internet</p>
</section>

<section class="platform">
  <div class="dash">
    <div class="abs" style="left:16px;top:14px;font-weight:600;color:#333;font-size:9px">QUENDRA</div>
    <div class="abs" style="left:10px;top:40px;width:78px">
      <div style="height:7px;background:var(--teal);margin-bottom:12px"></div><div style="height:7px;background:var(--teal);margin-bottom:12px"></div><div style="height:7px;background:var(--teal);margin-bottom:12px"></div><div style="height:7px;background:var(--teal);margin-bottom:12px"></div><div style="height:7px;background:var(--teal);margin-bottom:12px"></div><div style="height:7px;background:var(--teal);margin-bottom:12px"></div><div style="height:7px;background:var(--teal);margin-bottom:12px"></div><div style="height:7px;background:var(--teal);margin-bottom:12px"></div><div style="height:7px;background:var(--teal)"></div>
    </div>
    <div class="abs" style="left:110px;top:22px;color:var(--orange);font-weight:600;font-size:8px">Dashboard</div>
    <div class="abs" style="left:396px;top:20px;width:56px;height:10px;background:var(--teal)"></div>
    <div class="abs" style="left:110px;top:36px;width:240px;height:130px;border:1px solid #ddd">
      <div class="abs" style="left:6px;top:4px">History</div>
      <svg class="abs" style="left:14px;top:18px" width="200" height="100"><polygon points="0,92 20,74 34,82 60,60 76,70 124,44 176,30 196,34 196,92" fill="#e8d5b9"/><polyline points="0,92 20,74 34,82 60,60 76,70 124,44 176,30 196,34" fill="none" stroke="#8cb9b4" stroke-width="1.5"/><g fill="var(--teal)"><circle cx="20" cy="74" r="3"/><circle cx="60" cy="60" r="3"/><circle cx="124" cy="44" r="3"/><circle cx="176" cy="30" r="3"/></g><line x1="0" y1="92" x2="196" y2="92" stroke="#ccc"/></svg>
    </div>
    <div class="abs" style="left:360px;top:36px;width:96px;height:130px;border:1px solid #ddd">
      <div class="abs" style="left:6px;top:4px">Share Info</div>
      <div class="abs" style="left:6px;top:18px;width:82px;height:3px;background:#ddd"></div><div class="abs" style="left:6px;top:25px;width:70px;height:3px;background:#ddd"></div><div class="abs" style="left:6px;top:32px;width:78px;height:3px;background:#ddd"></div>
      <div class="abs" style="left:6px;top:84px;width:82px;height:10px;border:1px solid #ddd"></div>
      <div class="abs" style="left:30px;top:102px;width:40px;height:10px;background:var(--teal);color:#fff;text-align:center;line-height:10px">Save</div>
    </div>
    <div class="abs" style="left:110px;top:174px;width:100px;height:56px;border:1px solid #ddd"><div class="abs" style="left:6px;top:4px">Donut Stats</div><svg class="abs" style="left:20px;top:24px" width="60" height="32"><path d="M4 32a26 26 0 0 1 52 0" fill="none" stroke="#555" stroke-width="8"/></svg></div>
    <div class="abs" style="left:218px;top:174px;width:112px;height:56px;border:1px solid #ddd"><div class="abs" style="left:6px;top:4px">Tasks List</div><div class="abs" style="left:6px;top:22px;width:96px;height:8px;background:#eee"></div><div class="abs" style="left:6px;top:36px;width:96px;height:8px;background:#eee"></div><div class="abs" style="left:86px;top:22px;width:16px;height:8px;background:#6b6ed6"></div><div class="abs" style="left:86px;top:36px;width:16px;height:8px;background:#6b6ed6"></div></div>
    <div class="abs" style="left:338px;top:174px;width:118px;height:56px;border:1px solid #ddd"><div class="abs" style="left:6px;top:4px">Column Chart</div><div class="abs" style="left:6px;top:24px;width:80px;height:5px;background:#444"></div><div class="abs" style="left:6px;top:36px;width:60px;height:5px;background:#999"></div></div>
  </div>
  <h2><span class="dot"></span>ALL IN ONE GCR PLATFORM</h2>
  <p>Sed ut perspiciatis unde omnis iste natus error sit voluptatem accusantium doloremque laudantium, totam rem aperiam, eaque ipsa quae ab illo inventore veritatis et quasi architecto beatae vitae dicta sunt explicabo. Nemo enim ipsam voluptatem quia voluptas sit aspernatur aut odit aut fugit, sed quia consequuntur magni dolores eos qui ratione voluptatem sequi nesciunt. Neque porro quisquam est, qui</p>
</section>

<section class="cases">
  <h2 class="section-title"><span class="dot"></span>CASE STUDIES</h2>
</section>
<div class="case" style="left:96px;top:3506px;width:312px;height:418px">
  <div class="photo" role="img" aria-label="City office towers at dusk" style="height:180px;background:linear-gradient(180deg,#2b3f8f 0%,#3c4f9c 50%,#1c2440 100%)"></div>
  <h3 style="top:236px">Government Deployment across 150 Locations</h3>
  <p style="top:286px">During the initial assessment, a radio study was conducted to evaluate the feasibility of Wi-Fi in the building. It determined the Wi-Fi was not suitable.</p>
  <div class="btn" style="left:20px;top:370px">Read More</div>
</div>
<div class="case" style="left:422px;top:3477px;width:360px;height:475px">
  <div class="photo" role="img" aria-label="Hand inserting a module into server hardware" style="height:212px;background:linear-gradient(160deg,#d8d8d8 0%,#6f7168 45%,#2a2c2a 100%)"></div>
  <h3 style="top:270px">Exception Based Management Tools</h3>
  <p style="top:326px;font-size:15px;line-height:18px">During the initial assessment, a radio study was conducted to evaluate the feasibility of Wi-Fi in the building. It determined the Wi-Fi was not suitable.</p>
  <div class="btn" style="left:28px;top:416px;width:92px;height:26px;font-size:13px">Read More</div>
</div>
<div class="case" style="left:795px;top:3506px;width:312px;height:418px">
  <div class="photo" role="img" aria-label="Glass skyscrapers viewed from below" style="height:180px;background:linear-gradient(180deg,#b9c3cc 0%,#48525c 50%,#1b2127 100%)"></div>
  <h3 style="top:236px">Integration across disparate systems</h3>
  <p style="top:286px">During the initial assessment, a radio study was conducted to evaluate the feasibility of Wi-Fi in the building. It determined the Wi-Fi was not suitable.</p>
  <div class="btn" style="left:20px;top:370px">Read More</div>
</div>
<div class="arrow" style="left:31px"><svg width="14" height="18"><polyline points="11,2 3,9 11,16" fill="none" stroke="#fff" stroke-width="3"/></svg></div>
<div class="arrow" style="left:1121px"><svg width="14" height="18"><polyline points="3,2 11,9 3,16" fill="none" stroke="#fff" stroke-width="3"/></svg></div>

<section class="cta">
  <h2>ARE YOU READY TO ACCELERATE<br>YOUR BUSINESS?</h2>
  <p>Give us a call to learn more about<br>what we do at Quendra.....</p>
  <div class="btn">Get Started</div>
</section>

<footer class="site-footer">
  <div class="f-brand"><span class="dot"></span>QUENDRA</div>
  <div class="f-social"><span></span><span></span><span></span></div>
  <div class="f-col" style="left:337px">
    <h4>LINKS</h4>
    <ul class="f-links"><li>Solutions</li><li>Marketing</li><li>Case Studies</li></ul>
  </div>
  <div class="f-col" style="left:544px">
    <h4>CONTACT US</h4>
    <div class="f-contact"><span class="chip-icon"><svg width="16" height="16" viewBox="0 0 24 24"><path d="M6.6 10.8a15 15 0 0 0 6.6 6.6l2.2-2.2c.3-.3.7-.4 1-.2 1.1.4 2.3.6 3.6.6.6 0 1 .4 1 1V20c0 .6-.4 1-1 1A17 17 0 0 1 3 4c0-.6.4-1 1-1h3.5c.6 0 1 .4 1 1 0 1.3.2 2.5.6 3.6.1.3 0 .7-.2 1z" fill="var(--orange)"/></svg></span><div>PHONE:<br>1-555-014-2290</div></div>
    <div class="f-contact"><span class="chip-icon"><svg width="16" height="12"><rect x="1" y="1" width="14" height="10" rx="1" fill="none" stroke="var(--orange)" stroke-width="1.5"/><polyline points="1,1 8,7 15,1" fill="none" stroke="var(--orange)" stroke-width="1.5"/></svg></span><div>EMAIL:<br>info@quendra.com</div></div>
  </div>
  <div class="f-col f-news" style="left:818px">
    <h4>NEWSLETTER SIGN UP</h4>
    <p>To stay up to date on all the latest news &nbsp;from us</p>
    <div class="f-input">Email</div>
    <div class="f-sub">Subscribe</div>
  </div>
  <div class="f-rule"></div>
  <div class="f-copy">© 2024 Quendra. All Rights Reserved</div>
</footer>

</body>
</html>
```